Zielgruppe
Die Velorin Akademie bietet Kurse, Seminare & Coachings im Bereich der Kommunikation / Persönlichkeitsentwicklung an.
Folgendes Angebot besteht zur Zeit:
Seminare:
- 'Erste Schritte im Dialog', eine Einführung in die Kommunikation.
- 'Heitere Töchter, ruhige Väter' zum Thema Erziehung.
- 'Reifen mit Gelassenheit', zum Thema Älter werden und den Umgang damit.
Kurse:
- 'Gewaltfreie Kommunikation', Übungsgruppe
Coaching:
- Einzelsitzungen mit Hypnose
Ps: im Anhang unter 'Angabot_Vorlage.pdf' finden Sie mehr Infos zu den einezlenen Angebote.
Aufgabenstellung
Bitte berücksichtigen Sie, dass bereits ein Logo besteht (siehe Anhang).
Vom gesamteindruck her sollte die Website aufgeräumt, übersichtlich, harmonisch, freundlich & frisch wirken.
Es wäre super, wenn die Website authentisch wirkt (und weniger '0815 Business Website').
Bitte bedenken Sie, dass die Website sich an Private richtet, die sich nach einem 'strahlenderen & unbeschwerterem Lebene sehnen'.
Wir haben bereits viele Persönlichkeiten stärken können und möchten dies auch witerhin mit viel Herzblut machen.

```html
<!DOCTYPE html>
<html lang="de">
<head>
<meta charset="utf-8">
<title>Velorin Akademie – Heitere Töchter, ruhige Väter</title>
<link rel="stylesheet" href="https://fonts.googleapis.com/css2?family=Urbanist:wght@400;500;600&display=swap">
<style>
:root{
  --page:#ffffff;
  --ink:#3a3a3a;
  --muted:#5b5b5b;
  --panel:rgba(150,150,150,.82);
  --pill:#a9a9a9;
  --field:#f4f4f4;
  --footer:#f1f1f1;
  --deco:#efefef;
  --accent:#b8222e;
}
*{box-sizing:border-box;margin:0;padding:0}
html,body{width:1200px;height:2688px;overflow:hidden;background:var(--page);font-family:"Urbanist",sans-serif;color:var(--ink)}
.abs{position:absolute}
.desktop{position:absolute;left:34px;top:28px;width:922px;height:1854px;background:var(--page);box-shadow:0 0 18px rgba(0,0,0,.08);overflow:hidden}
.hero-photo{position:absolute;left:0;top:0;width:922px;height:580px;
  background:linear-gradient(to bottom,rgba(255,255,255,0) 60%,#fff 100%),
  linear-gradient(100deg,#3d4a2a 0%,#5d6b3e 28%,#c9c2ad 55%,#e8e4da 75%,#8d8f6a 100%)}
.brand{position:absolute;left:42px;top:40px;color:#fff;font-size:15px;font-weight:500;letter-spacing:3px;display:flex;align-items:center;gap:8px}
.brand i{width:10px;height:10px;border-radius:50%;background:#fff;display:block}
.nav{position:absolute;top:44px;left:0;width:922px;font-size:16px;color:#fff}
.nav span{position:absolute;top:0}
.nav .active{border:1.5px solid #fff;border-radius:4px;padding:3px 9px;top:-4px}
.hero-panel{position:absolute;left:42px;top:280px;width:431px;height:510px;background:var(--panel);border-radius:26px;padding:26px 22px;color:#fff}
.hero-panel h1{font-weight:500;font-size:34px;line-height:48px;letter-spacing:.2px;margin-bottom:10px}
.hero-panel p{font-size:13.5px;line-height:17px;margin-bottom:14px}
.facts .icon{position:absolute;left:520px}
.pill{position:absolute;left:576px;background:var(--pill);color:#fff;border-radius:10px;font-size:13.5px;padding:9px 16px;line-height:18px}
.form-title{position:absolute;left:0;width:922px;top:862px;text-align:center;font-size:34px;font-weight:500;color:#333}
.form-panel{position:absolute;left:156px;top:897px;width:610px;height:737px;overflow:hidden}
.form-photo{position:absolute;inset:0;background:linear-gradient(to bottom,#f7f7f7 0%,#d7d9db 28%,#a8a9ab 55%,#8b8b8b 80%,#7b7b7b 100%)}
.lbl{position:absolute;left:52px;font-size:17px;color:#3a3a3a}
.field{position:absolute;height:36px;background:var(--field);border-radius:7px;font-size:13.5px;padding:0 17px;line-height:36px;color:#333}
.field.select{background:#8e8e8e;color:#fff}
.btn{position:absolute;left:255px;top:473px;background:var(--field);border-radius:7px;font-size:13.5px;padding:0 14px;line-height:36px}
.consent{position:absolute;left:118px;top:557px;width:400px;font-size:13px;line-height:16px;color:#3e3e3e}
.footer{position:absolute;left:0;top:1692px;width:922px;height:162px;background:var(--footer);font-size:14px;color:#555}
.footer span{position:absolute}
.mobile{position:absolute;left:984px;top:28px;width:180px;height:942px;background:#f4f4f4;box-shadow:0 0 14px rgba(0,0,0,.1);overflow:hidden}
.m-photo{position:absolute;left:0;top:0;width:180px;height:260px;background:linear-gradient(to bottom,rgba(255,255,255,0) 70%,#f4f4f4 100%),linear-gradient(100deg,#4a5533,#b9b49c 55%,#e4e0d5 80%,#8c8e6b)}
.m-panel{position:absolute;left:8px;top:170px;width:164px;height:182px;background:var(--panel);border-radius:10px;padding:8px 6px;color:#fff}
.m-panel h2{font-size:6px;font-weight:600;text-align:center;margin-bottom:4px}
.m-panel p{font-size:3.6px;line-height:4.4px;margin-bottom:3px}
.m-pill{position:absolute;left:42px;background:var(--pill);color:#fff;border-radius:4px;font-size:3.8px;padding:4px 6px;line-height:5px}
.m-form{position:absolute;left:0;top:510px;width:180px;height:230px;background:linear-gradient(to bottom,#f4f4f4,#bfc0c2 40%,#858585)}
.m-lbl{position:absolute;left:15px;font-size:3.6px;color:#444}
.m-field{position:absolute;height:8px;background:#fff;border-radius:3px;font-size:3px;line-height:8px;padding-left:5px;color:#444}
.m-footer{position:absolute;left:0;top:760px;width:180px;text-align:center;font-size:9px;line-height:11px;color:#444}
</style>
</head>
<body>

<section class="desktop">
  <div class="hero-photo" role="img" aria-label="Foto: Vater und Mutter begleiten ihre Tochter auf dem Fahrrad in einer sonnigen Allee"></div>
  <div class="brand"><i></i>VELORIN AKADEMIE</div>
  <nav class="nav">
    <span style="left:285px">HOME</span>
    <span class="active" style="left:415px">ANGEBOTE</span>
    <span style="left:604px">KONTANKT</span>
    <span style="left:778px">ÜBER UNS</span>
  </nav>

  <article class="hero-panel">
    <h1>HEITERE TÖCHTER,<br>RUHIGE VÄTER</h1>
    <p>Unter Erziehung versteht man die pädagogische Einflussnahme auf die Entwicklung und das Verhalten heranwachsender“. Erziehungstheorien gibt es unzählige, die das Spektrum von streng und autoritär bis hin zum Laisser-faire decken.</p>
    <p>Das selbst erlebte wird z.T. auch unreflektiert wiederholt und/oder wir verlieren uns in unzählige Ratgeber.</p>
    <p>Mithilfe der Neurowissenschaften wird uns klar, dass das oft kräftezerrende Ringe rund um die Erziehung absolut unnötig und überflüssig ist, ja sogar schädigend. Am wirksamsten und effektivsten begleiten wir die Entwicklung eines Kindes mit Beziehung und Selbst-Erziehung – das ist die magische Formel. Indem wir zu nachahmenswerten Erwachsenen werden, fördern wir unsere eigene Persönlichkeitsentwicklung und ermöglichen damit eine harmonische, authentische und unterstützende Umgebung für die Kinder. Im 2. Teil gehen wir der Frage nach, wie Eltern ihre Kinder verhelfen zu starken, selbstsicheren und erfüllten Erwachsenen zu werden, die ihren eigenen Platz in der Gesellschaft kreieren jenseits von Konkurrenzkampf und Studiumsinflation</p>
  </article>

  <div class="facts">
    <svg class="icon" style="top:540px" width="46" height="64" viewBox="0 0 46 64" fill="#9a9a9a"><circle cx="14" cy="7" r="6"/><rect x="6" y="15" width="16" height="26" rx="3"/><rect x="8" y="40" width="5" height="22"/><rect x="15" y="40" width="5" height="22"/><rect x="20" y="17" width="20" height="4" rx="2"/></svg>
    <svg class="icon" style="top:618px" width="32" height="32" viewBox="0 0 32 32" fill="none" stroke="#9a9a9a" stroke-width="2.5"><circle cx="16" cy="16" r="13"/><path d="M16 8v8h6"/></svg>
    <svg class="icon" style="top:673px" width="36" height="36" viewBox="0 0 36 36" fill="none" stroke="#9a9a9a" stroke-width="2.5"><path d="M4 20 18 6h10v10L14 30z"/><circle cx="23" cy="11" r="2"/></svg>
    <svg class="icon" style="top:730px" width="28" height="38" viewBox="0 0 28 38" fill="#9a9a9a"><path d="M14 1C7 1 2 6 2 13c0 9 12 22 12 22s12-13 12-22C26 6 21 1 14 1zm0 17a5 5 0 1 1 0-10 5 5 0 0 1 0 10z"/><rect x="6" y="35" width="16" height="2"/></svg>
    <div class="pill" style="top:547px;width:298px">Was haben die Teilnehmer davon?<br>Entspanntes und erfülltes Leben mit Kindern</div>
    <div class="pill" style="top:630px">4 Abende à 1.5 Stunde</div>
    <div class="pill" style="top:687px">CHF 280.-</div>
    <div class="pill" style="top:744px">Luzern, Seehof</div>
  </div>

  <svg class="abs" style="left:0;top:900px" width="922" height="780" viewBox="0 0 922 780" fill="var(--deco)"><path d="M0 0 156 130V700L0 860z"/><path d="M922 40 830 0 766 60V400L850 740 922 670z"/></svg>

  <h2 class="form-title">JETZT ANMELDEN UND TEILNEHMEN!</h2>

  <form class="form-panel">
    <div class="form-photo" role="img" aria-label="Foto: junger Mann blickt auf eine nebelige Berglandschaft"></div>
    <span class="lbl" style="top:78px">NAME:</span>
    <span class="field" style="left:220px;top:68px;width:154px">VORNAME</span>
    <span class="field" style="left:404px;top:68px;width:154px">NACHNAME</span>
    <span class="lbl" style="top:136px">E-MAIL:</span>
    <span class="field" style="left:220px;top:125px;width:338px">E-MAIL ADRESSE</span>
    <span class="lbl" style="top:189px">ANSCHRIFT:</span>
    <span class="field" style="left:220px;top:181px;width:338px">ORT</span>
    <span class="field" style="left:220px;top:237px;width:338px">STRASSE</span>
    <span class="lbl" style="top:302px">GEBURTSDATUM:</span>
    <span class="field" style="left:220px;top:293px;width:338px">DATUM</span>
    <span class="lbl" style="top:360px">KURS:</span>
    <span class="field select" style="left:220px;top:350px;width:338px">HEITERE TÖCHTER, RUHIGE VÄTER
      <svg style="position:absolute;right:14px;top:12px" width="18" height="12" viewBox="0 0 18 12" fill="none" stroke="#fff" stroke-width="3"><path d="M2 2l7 7 7-7"/></svg></span>
    <span class="btn" style="left:254px;top:470px">ANMELDEN</span>
    <svg class="abs" style="left:118px;top:561px" width="15" height="15" viewBox="0 0 15 15"><rect width="15" height="15" rx="3" fill="var(--accent)"/><path d="M3.5 7.5l3 3 5-6" stroke="#fff" stroke-width="2" fill="none"/></svg>
    <div class="consent" style="left:141px">Dateschutz<br><span style="display:block;margin-top:8px">Die LEISTUNG habe ich gelesen und stimme der Speicherung meiner Daten zur weiteren Verarbeitung zu. Diese Einwilligung kann ich jederzeit widerrufen.</span></div>
  </form>

  <footer class="footer">
    <span style="left:88px;top:46px">VELORIN AKADEMIE</span>
    <span style="left:88px;top:82px">Lindenweg 8</span>
    <span style="left:88px;top:114px">54321 Talheim</span>
    <span style="left:281px;top:82px">Tel. 0123 98765432</span>
    <span style="left:281px;top:114px">Fax 0987 1234567</span>
    <span style="left:466px;top:82px">info@velorin-akademie.de</span>
    <span style="left:466px;top:114px">www.velorin-akademie.de</span>
    <span style="left:704px;top:82px">Impressum</span>
    <span style="left:704px;top:114px">Datenschutz</span>
  </footer>
</section>

<section class="mobile">
  <div class="m-photo" role="img" aria-label="Foto: Familie mit Kind auf dem Fahrrad"></div>
  <div class="abs" style="left:10px;top:12px;color:#fff;font-size:5px;letter-spacing:1px;font-weight:500">VELORIN AKADEMIE</div>
  <svg class="abs" style="left:152px;top:13px" width="16" height="12" viewBox="0 0 16 12" fill="#333"><rect width="16" height="2"/><rect y="5" width="16" height="2"/><rect y="10" width="16" height="2"/></svg>
  <div class="m-panel">
    <h2>HEITERE TÖCHTER, RUHIGE VÄTER</h2>
    <p>Unter Erziehung versteht man die pädagogische Einflussnahme auf die Entwicklung und das Verhalten heranwachsender“. Erziehungstheorien gibt es unzählige, die das Spektrum von streng und autoritär bis hin zum Laisser-faire decken.</p>
    <p>Das selbst erlebte wird z.T. auch unreflektiert wiederholt und/oder wir verlieren uns in unzählige Ratgeber.</p>
    <p>Mithilfe der Neurowissenschaften wird uns klar, dass das oft kräftezerrende Ringe rund um die Erziehung absolut unnötig und überflüssig ist, ja sogar schädigend. Am wirksamsten und effektivsten begleiten wir die Entwicklung eines Kindes mit Beziehung und Selbst-Erziehung – das ist die magische Formel. Indem wir zu nachahmenswerten Erwachsenen werden, fördern wir unsere eigene Persönlichkeitsentwicklung und ermöglichen damit eine harmonische, authentische und unterstützende Umgebung für die Kinder. Im 2. Teil gehen wir der Frage nach, wie Eltern ihre Kinder verhelfen zu starken, selbstsicheren und erfüllten Erwachsenen zu werden.</p>
  </div>
  <svg class="abs" style="left:14px;top:366px" width="16" height="28" viewBox="0 0 46 64" fill="#9a9a9a"><circle cx="14" cy="7" r="6"/><rect x="6" y="15" width="16" height="26" rx="3"/><rect x="8" y="40" width="5" height="22"/><rect x="15" y="40" width="5" height="22"/></svg>
  <svg class="abs" style="left:14px;top:410px" width="14" height="14" viewBox="0 0 32 32" fill="none" stroke="#9a9a9a" stroke-width="3"><circle cx="16" cy="16" r="13"/><path d="M16 8v8h6"/></svg>
  <svg class="abs" style="left:14px;top:436px" width="15" height="15" viewBox="0 0 36 36" fill="none" stroke="#9a9a9a" stroke-width="3"><path d="M4 20 18 6h10v10L14 30z"/></svg>
  <svg class="abs" style="left:16px;top:462px" width="11" height="15" viewBox="0 0 28 38" fill="#9a9a9a"><path d="M14 1C7 1 2 6 2 13c0 9 12 22 12 22s12-13 12-22C26 6 21 1 14 1z"/></svg>
  <div class="m-pill" style="top:370px;width:124px">Was haben die Teilnehmer davon?<br>Entspanntes und erfülltes Leben mit Kindern</div>
  <div class="m-pill" style="top:411px">4 Abende à 1.5 Stunde</div>
  <div class="m-pill" style="top:438px">CHF 280.-</div>
  <div class="m-pill" style="top:465px">Luzern, Seehof</div>
  <div class="abs" style="left:0;width:180px;top:514px;text-align:center;font-size:6.5px;color:#333">JETZT ANMELDEN UND TEILNEHMEN!</div>
  <div class="m-form" role="img" aria-label="Foto: Berglandschaft hinter dem Anmeldeformular"></div>
  <span class="m-lbl" style="top:540px">NAME:</span>
  <span class="m-field" style="left:64px;top:538px;width:44px">VORNAME</span>
  <span class="m-field" style="left:114px;top:538px;width:44px">NACHNAME</span>
  <span class="m-lbl" style="top:556px">E-MAIL:</span>
  <span class="m-field" style="left:64px;top:554px;width:94px">E-MAIL ADRESSE</span>
  <span class="m-lbl" style="top:572px">ANSCHRIFT:</span>
  <span class="m-field" style="left:64px;top:570px;width:94px">ORT</span>
  <span class="m-field" style="left:64px;top:586px;width:94px">STRASSE</span>
  <span class="m-lbl" style="top:604px">GEBURTSDATUM:</span>
  <span class="m-field" style="left:64px;top:602px;width:94px">DATUM</span>
  <span class="m-lbl" style="top:620px">KURS:</span>
  <span class="m-field" style="left:64px;top:618px;width:94px;background:#8e8e8e;color:#fff">HEITERE TÖCHTER, RUHIGE VÄTER</span>
  <span class="m-field" style="left:76px;top:642px;width:28px">ANMELDEN</span>
  <div class="abs" style="left:28px;top:672px;width:124px;font-size:3px;line-height:4px;color:#333">Dateschutz – Die LEISTUNG habe ich gelesen und stimme der Speicherung meiner Daten zur weiteren Verarbeitung zu. Diese Einwilligung kann ich jederzeit widerrufen.</div>
  <div class="m-footer">
    VELORIN AKADEMIE<br><br>Lindenweg 8<br>54321 Talheim<br><br>Tel. 0123 98765432<br>Fax 0987 1234567<br><br>info@velorin-akademie.de<br>www.velorin-akademie.de<br><br>Impressum<br>Datenschutz
  </div>
</section>

</body>
</html>
```